Business card for Eyelash extension salon in Westmere Hills,California USA

We need new business card for our salon in Westmere Hills. The salon name is 'Lashvera' . We would like to have...Business name: Lashvera Name of person: will provide later Address 4720 N.Alder Crest Ave Westmere Hills , CA 90099 Phone: will provide later (Text only) Web: www.lashverastudio.example Snapgrid icon, Circlebook icon follow us for seasonal campaign and news @lashverastudiolounge Design should look elegant, high-end, clean, simple, cohesive with my brand. Please refer my brand board. Business name color will be metallic bronzy color. Im thinking grey background or white background. Thanks

Target Market(s)

25-35. Gender neutral. People who are in Entertainment business industry.
This is High-end Eyelash extension salon in Westmere Hills

Industry/Entity Type

Beauty Salon

Contact Information for Business Card

Business name: Lashvera
Name of person: will provide later
Address 4720 N.Alder Crest Ave Westmere Hills , CA 90099
Phone: will provide later (Text only)
Web: www.lashverastudio.example
Snapgrid icon, Circlebook icon
follow us for seasonal campaign and news @lashverastudiolounge

Requirements
Must have
• Beautiful, elegant, clean and simple look but very attractive and modern
Should not have
• We don't like too clutter, too busy designs.

```html
<!DOCTYPE html>
<html lang="en">
<head>
<meta charset="utf-8">
<title>Lashvera Business Card</title>
<link rel="stylesheet" href="https://fonts.googleapis.com/css2?family=Bodoni+Moda:wght@500&family=Cormorant+Garamond:wght@400&family=Work+Sans:wght@400;500&display=swap">
<style>
  :root {
    --backdrop: #2a2a2a;
    --card: #f4f4f4;
    --bronze: #8a6a4f;
    --bronze-text: #7d604a;
    --icon-fg: #f4f4f4;
  }
  * { box-sizing: border-box; margin: 0; padding: 0; }
  html, body { width: 1200px; height: 800px; overflow: hidden; }
  body {
    background: var(--backdrop);
    position: relative;
    font-family: "Work Sans", sans-serif;
  }
  .card {
    position: absolute;
    width: 540px;
    height: 309px;
    background: var(--card);
    overflow: hidden;
    box-shadow: 0 18px 40px rgba(0,0,0,.45);
  }
  .card--front { left: 40px; top: 246px; }
  .card--back { left: 620px; top: 246px; }
  .rule { position: absolute; background: var(--bronze); }
  .rule--h { height: 1px; }
  .rule--v { width: 1px; }

  /* front */
  .brand {
    position: absolute;
    left: 0; right: 0; top: 98px;
    text-align: center;
    color: var(--bronze-text);
  }
  .brand__name {
    font-family: "Cormorant Garamond", serif;
    font-weight: 400;
    font-size: 66px;
    line-height: 1;
    letter-spacing: 1px;
  }
  .brand__place {
    font-family: "Work Sans", sans-serif;
    font-size: 7px;
    letter-spacing: 2.4px;
    margin-top: 6px;
  }
  .social {
    position: absolute;
    right: 40px; top: 250px;
    display: flex; align-items: center; gap: 14px;
    color: var(--bronze-text);
    font-size: 10px;
  }
  .social__item { display: flex; align-items: center; gap: 5px; }
  .social__dot {
    width: 9px; height: 9px; border-radius: 50%;
    background: var(--bronze);
  }

  /* back */
  .person {
    position: absolute;
    right: 40px; top: 38px;
    text-align: right;
    color: var(--bronze-text);
  }
  .person__name {
    font-family: "Bodoni Moda", serif;
    font-weight: 500;
    font-size: 20px;
    letter-spacing: .5px;
  }
  .person__role {
    font-size: 11px;
    font-weight: 500;
    letter-spacing: 2.5px;
    margin-top: 2px;
  }
  .contacts {
    position: absolute;
    left: 64px; top: 136px;
    list-style: none;
  }
  .contacts__item {
    display: flex; align-items: center;
    height: 32px;
    color: var(--bronze-text);
    font-size: 12.5px;
    letter-spacing: .3px;
    white-space: nowrap;
  }
  .contacts__icon {
    width: 20px; height: 20px; border-radius: 50%;
    background: var(--bronze);
    display: flex; align-items: center; justify-content: center;
    margin-right: 30px;
    flex: none;
  }
  .contacts__icon svg { width: 11px; height: 11px; }
</style>
</head>
<body>

  <section class="card card--front" aria-label="Card front">
    <span class="rule rule--h" style="left:0; top:24px; width:380px;"></span>
    <span class="rule rule--v" style="left:24px; top:0; height:250px;"></span>
    <span class="rule rule--v" style="left:514px; top:32px; height:277px;"></span>
    <span class="rule rule--h" style="left:330px; top:282px; width:210px;"></span>

    <div class="brand">
      <div class="brand__name">Lashvera</div>
      <div class="brand__place">WESTMERE HILLS</div>
    </div>

    <div class="social">
      <span class="social__item"><span class="social__dot"></span>Snapgrid</span>
      <span class="social__item"><span class="social__dot"></span>Circlebook</span>
      <span class="social__item">@lashverastudiolounge</span>
    </div>
  </section>

  <section class="card card--back" aria-label="Card back">
    <span class="rule rule--h" style="left:190px; top:96px; width:350px;"></span>
    <span class="rule rule--v" style="left:514px; top:0; height:160px;"></span>
    <span class="rule rule--v" style="left:108px; top:128px; height:181px;"></span>
    <span class="rule rule--h" style="left:0; top:282px; width:470px;"></span>
    <span class="rule rule--v" style="left:148px; top:262px; height:47px;"></span>

    <div class="person">
      <div class="person__name">MARISOL DENTRY</div>
      <div class="person__role">Manager</div>
    </div>

    <ul class="contacts">
      <li class="contacts__item">
        <span class="contacts__icon">
          <svg viewBox="0 0 12 12" aria-hidden="true"><path d="M6 1a3.5 3.5 0 0 0-3.5 3.5C2.5 7.3 6 11 6 11s3.5-3.7 3.5-6.5A3.5 3.5 0 0 0 6 1zm0 4.8a1.3 1.3 0 1 1 0-2.6 1.3 1.3 0 0 1 0 2.6z" fill="var(--icon-fg)"/></svg>
        </span>
        4720 N.Alder Crest Ave Westmere Hills , CA 90099
      </li>
      <li class="contacts__item">
        <span class="contacts__icon">
          <svg viewBox="0 0 12 12" aria-hidden="true"><rect x="3.2" y="1" width="5.6" height="10" rx="1" fill="none" stroke="var(--icon-fg)" stroke-width="1.1"/><circle cx="6" cy="9.3" r=".6" fill="var(--icon-fg)"/></svg>
        </span>
        555-214-0376
      </li>
      <li class="contacts__item">
        <span class="contacts__icon">
          <svg viewBox="0 0 12 12" aria-hidden="true" fill="none" stroke="var(--icon-fg)" stroke-width=".9"><circle cx="6" cy="6" r="4.6"/><ellipse cx="6" cy="6" rx="2" ry="4.6"/><path d="M1.4 6h9.2M2 3.8h8M2 8.2h8"/></svg>
        </span>
        www.lashverastudio.example
      </li>
      <li class="contacts__item">
        <span class="contacts__icon">
          <svg viewBox="0 0 12 12" aria-hidden="true" fill="none" stroke="var(--icon-fg)" stroke-width="1"><rect x="1.5" y="3" width="9" height="6.2" rx=".6"/><path d="M1.8 3.4 6 6.6l4.2-3.2"/></svg>
        </span>
        hello@lashverastudio.example
      </li>
    </ul>
  </section>

</body>
</html>
```